Need Business Card for our Real Estate Business with Sales Executive's Picture

PANTONE 484 C ( RED)

PANTONE 2766 C ( BLUE

Industry/Entity Type

Real Estate

Contact Information for Business Card

Name, Mobile, email, & picture of Person
Agency Phone, address, Web address

Requirements
Must have
• Our Logo Colours, Agent Picture,

```html
<!DOCTYPE html>
<html lang="en">
<head>
<meta charset="utf-8">
<title>Mirage Real Estate – Business Card</title>
<link rel="stylesheet" href="https://fonts.googleapis.com/css2?family=Cinzel:wght@500&family=Open+Sans:wght@400&display=swap">
<style>
  :root {
    --navy: #0b1640;
    --navy-ink: #1a2352;
    --paper: #ffffff;
    --backdrop: #e9e6e1;
    --photo-light: #c9cac3;
    --photo-dark: #2c4a9a;
    --text-light: #ffffff;
  }
  html, body {
    margin: 0;
    width: 1200px;
    height: 900px;
    overflow: hidden;
    background: var(--backdrop);
  }
  .canvas {
    width: 1200px;
    height: 900px;
    display: flex;
    align-items: center;
    justify-content: center;
    gap: 40px;
  }
  .card {
    width: 540px;
    height: 310px;
    position: relative;
    box-shadow: 0 6px 18px rgba(0,0,0,0.18);
    overflow: hidden;
  }
  /* Front */
  .card-front {
    background: var(--paper);
    display: flex;
    flex-direction: column;
    align-items: center;
    justify-content: center;
  }
  .brand-name {
    margin: 0;
    font-family: "Open Sans", sans-serif;
    font-weight: 400;
    font-size: 36px;
    line-height: 1.2;
    color: var(--navy);
  }
  .front-url {
    margin-top: 18px;
    font-family: "Open Sans", sans-serif;
    font-size: 14px;
    color: var(--navy-ink);
  }
  /* Back */
  .card-back {
    background: var(--navy);
  }
  .agent-photo {
    position: absolute;
    left: 60px;
    top: 48px;
    width: 214px;
    height: 214px;
    border-radius: 50%;
    background: linear-gradient(180deg, var(--photo-light) 0%, var(--photo-light) 55%, var(--photo-dark) 100%);
  }
  .agent-details {
    position: absolute;
    left: 308px;
    top: 62px;
    color: var(--text-light);
    font-family: "Open Sans", sans-serif;
  }
  .agent-name {
    font-family: "Cinzel", serif;
    font-weight: 500;
    font-size: 19px;
    letter-spacing: 0.5px;
    margin: 0 0 10px;
  }
  .contact-list {
    list-style: none;
    margin: 0;
    padding: 0;
    font-size: 12.5px;
    line-height: 20px;
  }
  .contact-list li {
    display: flex;
    align-items: center;
    gap: 7px;
  }
  .contact-list svg {
    width: 11px;
    height: 11px;
    fill: var(--text-light);
    flex: none;
  }
  .agent-address {
    margin: 6px 0 0 18px;
    font-size: 12.5px;
    line-height: 17px;
  }
</style>
</head>
<body>
<main class="canvas">
  <section class="card card-front" aria-label="Card front">
    <p class="brand-name">Mirage Real Estate</p>
    <div class="front-url">www.mirageestates.com</div>
  </section>

  <section class="card card-back" aria-label="Card back">
    <div class="agent-photo" role="img" aria-label="Portrait photo of the sales executive in a blue suit"></div>
    <div class="agent-details">
      <h1 class="agent-name">Daniel Carter</h1>
      <ul class="contact-list">
        <li><svg viewBox="0 0 24 24" aria-hidden="true"><path d="M6.6 10.8a15 15 0 0 0 6.6 6.6l2.2-2.2c.3-.3.7-.4 1-.2 1.1.4 2.3.6 3.6.6.6 0 1 .4 1 1V20c0 .6-.4 1-1 1A17 17 0 0 1 3 4c0-.6.4-1 1-1h3.5c.6 0 1 .4 1 1 0 1.3.2 2.5.6 3.6.1.3 0 .7-.2 1z"/></svg>044-555 010 234</li>
        <li><svg viewBox="0 0 24 24" aria-hidden="true"><path d="M7 1h10a2 2 0 0 1 2 2v18a2 2 0 0 1-2 2H7a2 2 0 0 1-2-2V3a2 2 0 0 1 2-2zm0 3v14h10V4zm5 15.5a1.2 1.2 0 1 0 0 2.4 1.2 1.2 0 0 0 0-2.4z"/></svg>044-555 010 234</li>
        <li><svg viewBox="0 0 24 24" aria-hidden="true"><path d="M2 5h20v14H2zm2 2v.5l8 5 8-5V7l-8 5z"/></svg>info@mirageestates.com</li>
        <li><svg viewBox="0 0 24 24" aria-hidden="true"><circle cx="12" cy="12" r="10"/></svg>www.mirageestates.com</li>
      </ul>
      <p class="agent-address">48 Palm Avenue, Dune City<br>Sunland, 560021.</p>
    </div>
  </section>
</main>
</body>
</html>
```